Business card for my new company (Accounting firm)

I need a business card for my new business Brightwell Advisory and Ledger SA. Our services are accounting, tax, audit and financial management. Our customers are small companies, start-ups and new companies. The final design has to show financial security, trust and growth. Please find our logo attached to the business card. Text for the business card: Brightwell Advisory and Ledger SA Tomas Varenholt Director and Founder Certified Accountant Tel. 022 418 57 34 tv@clairevalconseil.ch www.clairevalconseil.ch Rue des Vergières 27 1201 Geneva
Target Market(s)
Our customers are small companies, start-ups and new companies.
Industry/Entity Type
Finance And Accounting
Contact Information for Business Card
Claireval Conseil et Comptes SA
Tomas Varenholt
Directeur et Fondateur
Expert-comptable diplômé
Tél. 022 418 57 34
tv@clairevalconseil.ch
www.clairevalconseil.ch
Rue des Vergières 27
1201 Genève

```html
<!DOCTYPE html>
<html lang="fr">
<head>
<meta charset="utf-8">
<title>Claireval Conseil et Comptes SA – Carte de visite</title>
<link rel="stylesheet" href="https://fonts.googleapis.com/css2?family=Roboto:wght@400;500;700&display=swap">
<style>
  :root {
    --backdrop: #262525;
    --paper: #ffffff;
    --navy: #1a6291;
    --mid-blue: #2089c6;
    --sky-blue: #31afe0;
    --ink: #3d3d3d;
    --card-shadow: 0 4px 10px rgba(0,0,0,0.55);
  }
  * { margin: 0; padding: 0; box-sizing: border-box; }
  html, body {
    width: 1125px; height: 1200px; overflow: hidden;
    background: var(--backdrop);
    font-family: "Roboto", Arial, sans-serif;
  }
  .canvas { position: relative; width: 1125px; height: 1200px; }
  .card {
    position: absolute; left: 171px; width: 825px; height: 472px;
    overflow: hidden; box-shadow: var(--card-shadow);
  }
  .card--front { top: 106px; background: var(--paper); }
  .card--back { top: 639px; background: var(--sky-blue); }

  .front-waves { position: absolute; inset: 0; width: 100%; height: 100%; }

  .brand-front {
    position: absolute; left: 140px; top: 150px; width: 290px;
    text-align: center; color: var(--ink); font-weight: 500;
  }
  .brand-front__name { font-size: 44px; letter-spacing: 3px; line-height: 1; }
  .brand-front__tag { font-size: 15px; letter-spacing: 2.2px; margin-top: 8px; }

  .holder { position: absolute; left: 42px; top: 366px; color: var(--paper); }
  .holder__name { font-size: 30px; font-weight: 700; line-height: 1.1; margin-bottom: 4px; }
  .holder__role { font-size: 20px; font-weight: 400; line-height: 26px; }

  .contact {
    position: absolute; right: 34px; top: 306px;
    color: var(--paper); text-align: right; font-size: 19.5px; line-height: 25px;
  }
  .contact__address { margin-bottom: 10px; }
  .contact__line { display: flex; justify-content: flex-end; align-items: center; gap: 6px; line-height: 26px; }
  .contact__icon { width: 17px; height: 17px; flex: none; }

  .brand-back {
    position: absolute; right: 80px; top: 312px;
    color: var(--paper); font-weight: 500; text-align: left;
  }
  .brand-back__name { font-size: 56px; letter-spacing: 3px; line-height: 1; }
  .brand-back__tag { font-size: 21px; letter-spacing: 2.6px; margin-top: 8px; }
  .brand-back__web { font-size: 17px; letter-spacing: 3.2px; margin-top: 4px; font-weight: 400; }
</style>
</head>
<body>
<main class="canvas">

  <section class="card card--front" aria-label="Recto de la carte">
    <svg class="front-waves" viewBox="0 0 800 457" preserveAspectRatio="none" aria-hidden="true">
      <defs>
        <linearGradient id="bandGradient" x1="0" y1="0" x2="1" y2="0">
          <stop offset="0" stop-color="#31afe0"/>
          <stop offset="0.45" stop-color="#31afe0"/>
          <stop offset="0.7" stop-color="#2089c6"/>
          <stop offset="1" stop-color="#2089c6"/>
        </linearGradient>
      </defs>
      <path d="M0,215 C120,290 300,302 400,296 C560,282 700,150 765,0 L800,0 L800,457 L0,457 Z" fill="url(#bandGradient)"/>
      <path d="M0,276 C150,314 380,318 500,290 C640,256 750,122 800,0" fill="none" stroke="#ffffff" stroke-width="2.5"/>
      <path d="M0,283 C150,321 380,324 502,296 C642,262 752,128 800,8 L800,457 L0,457 Z" fill="#1a6291"/>
    </svg>

    <div class="brand-front">
      <div class="brand-front__name">CLAIREVAL</div>
      <div class="brand-front__tag">CONSEIL ET COMPTES</div>
    </div>

    <div class="holder">
      <div class="holder__name">Tomas Varenholt</div>
      <div class="holder__role">Directeur et Fondateur</div>
      <div class="holder__role">Expert-comptable diplômé</div>
    </div>

    <div class="contact">
      <div class="contact__address">Rue des Vergières 27<br>1201 Genève</div>
      <div class="contact__line">022 418 57 34
        <svg class="contact__icon" viewBox="0 0 24 24" aria-hidden="true"><path fill="#fff" d="M6.6 10.8a15.1 15.1 0 0 0 6.6 6.6l2.2-2.2a1 1 0 0 1 1-.25 11.4 11.4 0 0 0 3.6.57 1 1 0 0 1 1 1V20a1 1 0 0 1-1 1A17 17 0 0 1 3 4a1 1 0 0 1 1-1h3.5a1 1 0 0 1 1 1c0 1.25.2 2.45.57 3.57a1 1 0 0 1-.25 1z"/></svg>
      </div>
      <div class="contact__line">tv@clairevalconseil.ch
        <svg class="contact__icon" viewBox="0 0 24 24" aria-hidden="true"><rect x="2" y="5" width="20" height="14" fill="#fff"/><path d="M2 5l10 8 10-8" fill="none" stroke="#1a6291" stroke-width="1.8"/></svg>
      </div>
      <div class="contact__line">www.clairevalconseil.ch
        <svg class="contact__icon" viewBox="0 0 24 24" aria-hidden="true"><circle cx="12" cy="12" r="10" fill="#fff"/><path d="M12 2v20M2 12h20M12 2c-4 3-4 17 0 20M12 2c4 3 4 17 0 20" fill="none" stroke="#1a6291" stroke-width="1.4"/></svg>
      </div>
    </div>
  </section>

  <section class="card card--back" aria-label="Verso de la carte">
    <div class="brand-back">
      <div class="brand-back__name">CLAIREVAL</div>
      <div class="brand-back__tag">CONSEIL ET COMPTES</div>
      <div class="brand-back__web">www.clairevalconseil.ch</div>
    </div>
  </section>

</main>
</body>
</html>
```